Torvel’s letterhead for local government

I require a letterhead for quarterly communications with constituents. The colours I have used in the past are navy & green (together) so I’m happy to use similar colours for this. Please refer to business card as an example.
The letter must make reference to the position I hold which is as per below
“Clr Torvel Quennisbury OAM”
And the tag line I have used in the past is “Torvel on the Terrace”. Although I’m not sure if this would be used in a letterhead or not. Happy for this to be provided as an option.
I would like a photo in the letterhead as I believe face recognition is key as an elected member.

Target Market(s)

Political interests

Industry/Entity Type

Government Office

Font styles to use
Sans Serif

Requirements
Must have
• Politically professional. I have been an elected member for 2 years so it is expected that the letterhead conveys that. The colours of the business card is to be used.
Nice to have
• Background of photos to be manipulated or changed to make me stand out, if possible?
Should not have
• Looked like it’s cropped or undertaken by an amateur designer.

```html
<!DOCTYPE html>
<html lang="en">
<head>
<meta charset="utf-8">
<title>Torvel Quennisbury – Letterhead</title>
<link rel="stylesheet" href="https://fonts.googleapis.com/css2?family=Arimo:wght@400;700&family=Open+Sans:wght@400;600&display=swap">
<style>
  :root {
    --navy: #2a5d8f;
    --green: #44b665;
    --paper: #ffffff;
    --backdrop: #e6e6e6;
    --ink: #444444;
    --ink-strong: #333333;
    --photo-tone: #3d4c66;
  }
  * { box-sizing: border-box; margin: 0; padding: 0; }
  html, body {
    width: 1040px; height: 1200px; overflow: hidden;
    background: var(--backdrop);
  }
  .letterhead {
    position: absolute; left: 62px; top: 10px;
    width: 790px; height: 1017px;
    background: var(--paper);
    transform: scale(1.16); transform-origin: top left;
    font-family: "Open Sans", Arial, sans-serif;
    color: var(--ink);
    box-shadow: 0 1px 4px rgba(0,0,0,.15);
  }
  .masthead { position: absolute; left: 0; top: 0; width: 790px; height: 182px; }
  .masthead svg, .contact-bar svg { position: absolute; left: 0; top: 0; display: block; }
  .portrait {
    position: absolute; left: 132px; top: 9px; width: 147px; height: 164px;
    border-radius: 60px 60px 0 0;
    background: linear-gradient(180deg, #8a6b5a 0%, #6e6a78 35%, var(--photo-tone) 100%);
  }
  .identity {
    position: absolute; left: 296px; top: 48px; color: #fff;
    font-family: "Arimo", Arial, sans-serif;
  }
  .identity .member-name { font-size: 27px; font-weight: 700; letter-spacing: -0.2px; line-height: 32px; }
  .identity .role { font-size: 20px; line-height: 25px; margin-top: 6px; }
  .letter-body {
    position: absolute; left: 74px; top: 216px; width: 638px;
    font-size: 12.5px; line-height: 23px;
  }
  .issue-date { margin-bottom: 8px; }
  .recipient { line-height: 15.5px; margin-bottom: 42px; }
  .salutation { margin-bottom: 23px; }
  .letter-body p.copy { text-align: justify; margin-bottom: 23px; hyphens: auto; }
  .closing { margin-top: 45px; }
  .signatory { margin-top: 44px; font-size: 15px; font-weight: 600; color: var(--ink-strong); line-height: 20px; }
  .signatory-title { font-size: 12.5px; line-height: 20px; }
  .contact-bar { position: absolute; left: 0; top: 928px; width: 790px; height: 89px; }
  .contact-line {
    position: absolute; left: 91px; top: 52px; color: #fff;
    font-family: "Arimo", Arial, sans-serif; font-size: 15px; white-space: nowrap;
  }
  .contact-line .sep { margin: 0 12px; }
</style>
</head>
<body>
  <article class="letterhead">
    <header class="masthead">
      <svg width="790" height="182" viewBox="0 0 790 182">
        <rect width="790" height="182" fill="var(--navy)"/>
        <polygon points="0,182 790,143 790,182" fill="#fff"/>
        <polygon points="0,182 790,147 790,182" fill="var(--green)"/>
      </svg>
      <div class="portrait" role="img" aria-label="Portrait photo of Torvel Quennisbury in a dark suit holding a folder"></div>
      <div class="identity">
        <div class="member-name">Clr Torvel Quennisbury OAM</div>
        <div class="role">Area Councillor<br>City of Harrowmere</div>
      </div>
    </header>

    <section class="letter-body">
      <div class="issue-date">Issuing Date: May 5, 2018</div>
      <div class="recipient">Name Of Employee Mr. XYZABC<br>Address of Employee<br>Address Line 2 etc..</div>
      <div class="salutation">Dear Mr.XYZABC</div>
      <p class="copy">Lorem Ipsum has been the industry's standard dummy text ever since the 1500s, when an unknown printer took a galley of type and scrambled it to make a type specimen book. It has survived not only five centuries, but also the leap into electronic typesetting, remaining essentially unchanged. It was popularised in the 1960s with the release of Pressline sheets containing Lorem Ipsum passages, and more recently with desktop publishing software like Quillset Layout including versions of Lorem Ipsum.</p>
      <p class="copy">Lorem Ipsum is simply dummy text of the printing and typesetting industry. Lorem Ipsum has been the industry's standard dummy text ever since the 1500s, when an unknown printer took a galley of type and scrambled it to make a type specimen book.</p>
      <p class="copy">It has survived not only five centuries, but also the leap into electronic typesetting, remaining essentially unchanged. It was popularised in the 1960s with the release of Pressline sheets containing Lorem IpsumIpsum passages.</p>
      <div class="closing">Yours Sincerely</div>
      <div class="signatory">Delwyn Marsh</div>
      <div class="signatory-title">Managing Director</div>
    </section>

    <footer class="contact-bar">
      <svg width="790" height="89" viewBox="0 0 790 89">
        <polygon points="0,0 790,0 790,33 0,6" fill="var(--green)"/>
        <polygon points="0,6 790,33 790,37 0,8" fill="#fff"/>
        <polygon points="0,8 790,37 790,89 0,89" fill="var(--navy)"/>
      </svg>
      <div class="contact-line">P: 041-555 018 274<span class="sep">|</span>E:&nbsp; hello@quennisbury.org<span class="sep">|</span>www.quennisbury.org</div>
    </footer>
  </article>
</body>
</html>
```